All-Natural Head Lice Removal company

I need a business card with my pre-existing logo. We are a new company located in Portland Oregon that goes into peoples homes to help with head lice removal. My products and approach are all- natural and also will be around children.On my current logo we used Teal Bl and the color Green. I am open to new ideas just want it simple and creative

Target Market(s)

my biggest market is families of school aged children

Industry/Entity Type

Business

Contact Information for Business Card

see upload for details from previous business card

Font styles to use
Serif

Colors
33a6d7
9bcb3b
f37122

Requirements
Must have
• Basic information/ logo put into a creative format that is catching to the eye
Nice to have
• creative

```html
<!DOCTYPE html>
<html lang="en">
<head>
<meta charset="utf-8">
<title>Nit Nomad Business Cards</title>
<link rel="stylesheet" href="https://fonts.googleapis.com/css2?family=Arvo:wght@400;700&display=swap">
<style>
  :root {
    --blue: #33a6d7;
    --blue-light: #93d5f1;
    --green: #9bcb3b;
    --ink: #2e2e30;
    --white: #ffffff;
    --backdrop: #ece9e4;
  }
  * { box-sizing: border-box; margin: 0; padding: 0; }
  html, body { width: 1200px; height: 913px; overflow: hidden; }
  body {
    background: var(--backdrop);
    font-family: "Arvo", Georgia, serif;
    color: var(--ink);
    position: relative;
  }
  .card {
    position: absolute;
    top: 302px;
    width: 540px;
    height: 309px;
    background: var(--white);
    border-radius: 18px;
    overflow: hidden;
    box-shadow: 0 6px 18px rgba(0,0,0,0.18);
  }
  .card--front { left: 40px; }
  .card--back { left: 620px; }
  .card__shapes { position: absolute; inset: 0; }

  .brand {
    position: absolute;
    display: flex;
    align-items: center;
    gap: 12px;
  }
  .brand__dot {
    width: 34px; height: 34px;
    border-radius: 50%;
    background: var(--green);
  }
  .brand__name {
    font-weight: 700;
    font-size: 34px;
    color: var(--ink);
    white-space: nowrap;
  }
  .card--front .brand { left: 34px; top: 134px; }
  .card--back .brand { left: 50%; top: 70px; transform: translateX(-50%); }

  .front-info {
    position: absolute;
    right: 34px;
    top: 30px;
    text-align: right;
    color: var(--white);
  }
  .front-info__service { font-size: 13px; line-height: 1.3; width: 190px; margin-left: auto; }
  .front-info__name { font-size: 21px; font-weight: 700; margin-top: 28px; letter-spacing: 0.5px; }
  .front-info__role { font-size: 10px; color: var(--ink); letter-spacing: 1px; margin-top: 2px; }
  .contact-list { list-style: none; margin-top: 22px; font-size: 14px; line-height: 1.55; }
  .contact-list li { display: flex; justify-content: flex-end; align-items: center; gap: 8px; }
  .contact-list svg { width: 12px; height: 12px; flex: none; }

  .back-tagline {
    position: absolute;
    left: 0; right: 0;
    top: 150px;
    text-align: center;
    font-weight: 700;
    font-size: 14px;
    line-height: 1.35;
  }
  .back-web {
    position: absolute;
    right: 70px;
    top: 246px;
    font-size: 14px;
    font-weight: 700;
  }
</style>
</head>
<body>

<section class="card card--front" aria-label="Business card front">
  <svg class="card__shapes" viewBox="0 0 540 309" aria-hidden="true">
    <defs>
      <linearGradient id="front-sky" x1="0" y1="0" x2="0" y2="1">
        <stop offset="0" stop-color="var(--blue-light)"/>
        <stop offset="1" stop-color="var(--blue)"/>
      </linearGradient>
    </defs>
    <path d="M170 0 L540 0 L540 309 L300 309 Q300 70 170 0 Z" fill="url(#front-sky)"/>
    <path d="M170 0 Q300 70 300 309" fill="none" stroke="var(--ink)" stroke-width="3"/>
    <path d="M540 52 A14 14 0 0 0 540 80 Z" fill="var(--ink)"/>
  </svg>

  <div class="brand">
    <span class="brand__dot"></span>
    <span class="brand__name">Nit Nomad</span>
  </div>

  <div class="front-info">
    <p class="front-info__service">All Natural In-Home Lice Removal Services</p>
    <p class="front-info__name">DANA WHITLOCK</p>
    <p class="front-info__role">OWNER</p>
    <ul class="contact-list">
      <li>1-855-555-NITS (6487)
        <svg viewBox="0 0 12 12"><path d="M3 1 L5 3 L4 4.5 Q5 7 7.5 8 L9 7 L11 9 L9.5 11 Q4 10.5 1 3 Z" fill="var(--ink)"/></svg>
      </li>
      <li>Dana@NitNomad.com
        <svg viewBox="0 0 12 12"><rect x="1" y="2.5" width="10" height="7" fill="none" stroke="var(--ink)" stroke-width="1.2"/><path d="M1 2.5 L6 6.5 L11 2.5" fill="none" stroke="var(--ink)" stroke-width="1.2"/></svg>
      </li>
      <li>www.NitNomad.com
        <svg viewBox="0 0 12 12"><circle cx="6" cy="6" r="5" fill="none" stroke="var(--ink)" stroke-width="1.2"/><ellipse cx="6" cy="6" rx="2.2" ry="5" fill="none" stroke="var(--ink)" stroke-width="1"/><path d="M1 6 H11" stroke="var(--ink)" stroke-width="1"/></svg>
      </li>
    </ul>
  </div>
</section>

<section class="card card--back" aria-label="Business card back">
  <svg class="card__shapes" viewBox="0 0 540 309" aria-hidden="true">
    <defs>
      <linearGradient id="back-sky" x1="0" y1="0" x2="1" y2="1">
        <stop offset="0" stop-color="var(--blue-light)"/>
        <stop offset="1" stop-color="var(--blue)"/>
      </linearGradient>
    </defs>
    <path d="M190 309 Q270 205 540 185 L540 309 Z" fill="url(#back-sky)"/>
  </svg>

  <div class="brand">
    <span class="brand__dot"></span>
    <span class="brand__name">Nit Nomad</span>
  </div>

  <p class="back-tagline">Try Nit Nomad Today and Be Lice Free Tomorrow!<br>All Natural In-Home Lice Removal Services</p>
  <p class="back-web">www.NitNomad.com</p>
</section>

</body>
</html>
```